Velundra Jobs portal

Velundra Jobs is a job portal connecting job seekers and companies offering part time jobs in the Mena region, starting in the UAE. We would like to see designs that use the color blue. We have attached images to give an idea what the website should look like. When a company posts a job the job seekers are not allowed to see which company has posted a job. There should also be a coinvex gateway. On the landing page we want a catching picture that we will send.

Target Market(s)

Students and promotional workers

Logo Text

Velundra Jobs

Coding

Coded - Design and coding required

Number of Pages Required

4 page

Font styles to use
Sans Serif

Colors
33a6d7
0692cd
85cae6

```html
<!DOCTYPE html>
<html lang="en">
<head>
<meta charset="utf-8">
<title>Velundra Jobs</title>
<link href="https://fonts.googleapis.com/css2?family=Open+Sans:wght@400;600&display=swap" rel="stylesheet">
<style>
:root{
  --pink:#e4468b;
  --pink-box:rgba(232,92,155,.88);
  --maroon:#6e0f38;
  --blue-dark:#1f4c9c;
  --blue:#2c5fb6;
  --blue-line:#4a78c6;
  --teal:#4fc0c6;
  --teal-dark:#39a9b0;
  --teal-footer:#4bbdbb;
  --teal-bar:#6ad2d5;
  --teal-btn:#0e6663;
  --link-blue:#1f64b8;
  --text:#333;
  --line:#dcdcdc;
}
*{box-sizing:border-box;margin:0;padding:0}
html,body{width:1034px;height:1200px;overflow:hidden;background:#fff;font-family:"Open Sans",sans-serif;color:var(--text)}
.page{position:relative;width:1034px;height:1200px}
.abs{position:absolute}

.header{position:absolute;left:0;top:0;width:1034px;height:81px;background:linear-gradient(#fdfdfd,#efefef);border-bottom:1px solid #ddd}
.logo{left:185px;top:14px;font-size:34px;font-weight:400;color:#3aa8c4;letter-spacing:-.5px}
.nav a{position:absolute;top:33px;font-size:13px;color:#333;text-decoration:none}
.sep{position:absolute;top:0;width:1px;height:80px;background:#d6d6d6}
.badge{left:686px;top:18px;width:17px;height:17px;border-radius:50%;background:var(--teal);color:#fff;font-size:7px;line-height:17px;text-align:center}
.avatar{left:724px;top:23px;width:35px;height:35px;border-radius:50%;background:radial-gradient(#c9a58e,#6b5a55)}
.username{left:723px;top:61px;font-size:7px;color:#555}
.logout{left:782px;top:28px;width:64px;height:25px;border-radius:13px;background:var(--pink);color:#fff;font-size:11px;line-height:25px;text-align:center}

.hero{left:0;top:81px;width:1034px;height:253px;background:linear-gradient(90deg,#c9d5e2,#e7d8cb 30%,#d9d6d6 55%,#cfc6c1 80%,#b99279)}
.search-box{left:183px;top:155px;width:650px;height:119px;background:var(--pink-box)}
.search-box h1{position:absolute;left:20px;top:20px;font-size:19px;font-weight:400;color:#fff}
.search-box p{position:absolute;left:21px;top:45px;font-size:9.5px;color:#fff}
.field{position:absolute;top:68px;width:128px;height:26px;background:#fff;border:1px solid #ddd;font-size:8.5px;color:#888;line-height:24px;padding-left:10px}
.filter-btn{position:absolute;left:563px;top:67px;width:74px;height:28px;background:var(--maroon);border:1px solid #4a0a25;color:#fff;font-size:10px;line-height:26px;text-align:center}

.categories{left:183px;top:366px;width:195px;height:339px;background:var(--blue)}
.categories h2{height:41px;background:var(--blue-dark);color:#fff;font-size:14px;font-weight:400;padding:11px 0 0 22px}
.cat-list{list-style:none;padding-top:3px}
.cat-list li{height:21.7px;border-bottom:1px solid var(--blue-line);display:flex;justify-content:space-between;padding:5px 27px 0 31px;font-size:9.5px;color:#fff}

.jobs{left:397px;top:370px;width:454px;height:335px;border:1px solid var(--line);background:#f3f3f3}
.jobs-head{height:35px;background:linear-gradient(var(--teal),var(--teal-dark));color:#fff;font-size:11.5px;position:relative}
.jobs-head span{position:absolute;top:11px;display:flex;align-items:center;gap:5px}
.job-row{position:absolute;left:0;width:452px;height:44px;background:#fff;border-bottom:1px solid var(--line)}
.job-title{position:absolute;left:14px;top:8px;font-size:10.5px;color:#333}
.job-desc{position:absolute;left:15px;top:29px;font-size:6.5px;color:#999}
.due{position:absolute;left:188px;top:14px;font-size:6.5px;color:#888}
.date{position:absolute;left:188px;top:26px;font-size:8px;color:#777}
.apply{position:absolute;left:360px;top:12px;width:75px;height:21px;background:var(--pink);color:#fff;font-size:9px;font-weight:600;line-height:21px;text-align:center}

.featured-title{left:182px;top:748px;font-size:17px;font-weight:400;color:#333}
.card{position:absolute;top:787px;width:157px}
.card-photo{width:157px;height:78px}
.card h3{margin-top:9px;font-size:11.5px;font-weight:400;color:var(--link-blue)}
.card p{margin-top:3px;font-size:7px;line-height:12px;color:#777}
.card .click{display:inline-block;margin-top:6px;width:58px;height:18px;border:1px solid var(--teal);font-size:7.5px;line-height:16px;text-align:center;color:var(--teal)}

.footer{left:0;top:984px;width:1034px;height:168px;background:var(--teal-footer)}
.col{position:absolute;top:32px;color:#fff}
.col h4{font-size:16px;font-weight:400;margin-bottom:8px}
.col a,.col div{display:block;font-size:9.5px;line-height:18.5px;color:#fff;text-decoration:none}
.col .email{width:179px;height:24px;background:#fff;border-radius:2px;margin-top:7px;font-size:7px;color:#555;line-height:24px;padding-left:10px}
.col .subscribe{width:81px;height:26px;background:var(--teal-btn);margin-top:7px;font-size:10px;line-height:26px;text-align:center}
.col .phone{font-size:12px}
.bottom-bar{left:0;top:1152px;width:1034px;height:48px;background:var(--teal-bar)}
.bottom-bar p{position:absolute;left:183px;top:18px;font-size:8px;color:#fff}
</style>
</head>
<body>
<div class="page">

  <header class="header">
    <div class="abs logo">velundra</div>
    <nav class="nav"><a style="left:423px" href="#">About Us</a><a style="left:515px" href="#">Contact Us</a></nav>
    <div class="sep" style="left:598px"></div>
    <div class="sep" style="left:655px"></div>
    <div class="sep" style="left:709px"></div>
    <svg class="abs" style="left:616px;top:30px" width="22" height="22" viewBox="0 0 22 22"><circle cx="9" cy="9" r="6.5" fill="none" stroke="#2a5fb0" stroke-width="3"/><line x1="14" y1="14" x2="20" y2="20" stroke="#2a5fb0" stroke-width="3.5" stroke-linecap="round"/></svg>
    <svg class="abs" style="left:674px;top:30px" width="20" height="21" viewBox="0 0 20 21"><path d="M10 1c4 0 6 3 6 7v5l3 3H1l3-3V8c0-4 2-7 6-7z" fill="#2a5fb0"/><circle cx="10" cy="18.5" r="2.3" fill="#2a5fb0"/></svg>
    <div class="abs badge">23</div>
    <div class="abs avatar" role="img" aria-label="User profile photo"></div>
    <div class="abs username">Username</div>
    <div class="abs logout">Logout</div>
  </header>

  <section class="abs hero" role="img" aria-label="Photo of smiling colleagues in a business meeting"></section>

  <div class="abs search-box">
    <h1>JOB SEEKERS</h1>
    <p>Mauris vel lacus vitae felis vestibulum volutpat Etiam est nunc venenatis in tristique eu imperdiet ac nisl</p>
    <div class="field" style="left:21px">Keyword</div>
    <div class="field" style="left:156px">District</div>
    <div class="field" style="left:291px">Job</div>
    <div class="field" style="left:425px">Language Spoken</div>
    <div class="filter-btn">Filter Now</div>
  </div>

  <aside class="abs categories">
    <h2>Choose By Category</h2>
    <ul class="cat-list">
      <li><span>Integer congue augue</span><span>(04)</span></li>
      <li><span>Et malesuada</span><span>(15)</span></li>
      <li><span>Aaculis ipsum</span><span>(10)</span></li>
      <li><span>Dui aliquet felis</span><span>(09)</span></li>
      <li><span>Cursus magna</span><span>(11)</span></li>
      <li><span>Nisl nec elit</span><span>(05)</span></li>
      <li><span>Praesent elementum</span><span>(04)</span></li>
      <li><span>Elit at tellus</span><span>(15)</span></li>
      <li><span>Nec ultricies</span><span>(10)</span></li>
      <li><span>Sit amet porttitor</span><span>(09)</span></li>
      <li><span>Mattis enim</span><span>(11)</span></li>
      <li><span>Libero interdum</span><span>(02)</span></li>
      <li><span>Nec interdum</span><span>(05)</span></li>
    </ul>
  </aside>

  <section class="abs jobs">
    <div class="jobs-head">
      <span style="left:14px"><svg width="15" height="15" viewBox="0 0 15 15"><circle cx="7.5" cy="7.5" r="7.5" fill="#fff"/><rect x="6.4" y="6" width="2.2" height="6" fill="#45b6bd"/><circle cx="7.5" cy="3.8" r="1.3" fill="#45b6bd"/></svg>Job tittle</span>
      <span style="left:231px"><svg width="15" height="15" viewBox="0 0 15 15"><rect x="1" y="2.5" width="13" height="11.5" fill="none" stroke="#fff" stroke-width="1.4"/><rect x="1" y="2.5" width="13" height="3" fill="#fff"/><path d="M4 8h2M7 8h2M10 8h2M4 11h2M7 11h2M10 11h2" stroke="#fff" stroke-width="1.2"/></svg>Date</span>
    </div>
    <div class="job-row" style="top:36px"><div class="job-title">Your Job Tittle goes here</div><div class="job-desc">Proin nulla arcu nonummy luctus dictum eget</div><div class="due">Due Date</div><div class="date">25 April 2015</div><div class="apply">APPLY NOW</div></div>
    <div class="job-row" style="top:82px"><div class="job-title">Your Job Tittle goes here</div><div class="job-desc">Proin nulla arcu nonummy luctus dictum eget</div><div class="due">Due Date</div><div class="date">25 April 2015</div><div class="apply">APPLY NOW</div></div>
    <div class="job-row" style="top:130px"><div class="job-title">Your Job Tittle goes here</div><div class="job-desc">Proin nulla arcu nonummy luctus dictum eget</div><div class="due">Due Date</div><div class="date">25 April 2015</div><div class="apply">APPLY NOW</div></div>
    <div class="job-row" style="top:174px"><div class="job-title">Your Job Tittle goes here</div><div class="job-desc">Proin nulla arcu nonummy luctus dictum eget</div><div class="due">Due Date</div><div class="date">25 April 2015</div><div class="apply">APPLY NOW</div></div>
    <div class="job-row" style="top:225px"><div class="job-title">Your Job Tittle goes here</div><div class="job-desc">Proin nulla arcu nonummy luctus dictum eget</div><div class="due">Due Date</div><div class="date">25 April 2015</div><div class="apply">APPLY NOW</div></div>
    <div class="job-row" style="top:269px"><div class="job-title">Your Job Tittle goes here</div><div class="job-desc">Proin nulla arcu nonummy luctus dictum eget</div><div class="due">Due Date</div><div class="date">25 April 2015</div><div class="apply">APPLY NOW</div></div>
  </section>

  <h2 class="abs featured-title">Featured Job Provider</h2>
  <div class="card" style="left:183px"><div class="card-photo" role="img" aria-label="Photo of a smiling businesswoman at a laptop" style="background:linear-gradient(90deg,#c7c9cc,#9a7a6a 55%,#d8d8d8)"></div><h3>Mauris vel lacus vitae</h3><p>pede Fusce tellus Sed metus augue convallis et vehicula ut pulvinar eu ante Integer orci</p><span class="click">Click here</span></div>
  <div class="card" style="left:354px"><div class="card-photo" role="img" aria-label="Photo of colleagues working together at a desk" style="background:linear-gradient(90deg,#b9b6b3,#d9cfc4 50%,#a9aeb6)"></div><h3>Mauris vel lacus vitae</h3><p>pede Fusce tellus Sed metus augue convallis et vehicula ut pulvinar eu ante Integer orci</p><span class="click">Click here</span></div>
  <div class="card" style="left:524px"><div class="card-photo" role="img" aria-label="Photo of a man with glasses at a computer" style="background:linear-gradient(90deg,#c9d0d6,#8d9eb2 55%,#dfe2e5)"></div><h3>Mauris vel lacus vitae</h3><p>pede Fusce tellus Sed metus augue convallis et vehicula ut pulvinar eu ante Integer orci</p><span class="click">Click here</span></div>
  <div class="card" style="left:694px"><div class="card-photo" role="img" aria-label="Photo of a woman with glasses in an office" style="background:linear-gradient(90deg,#a2a0a4,#d8c7b5 45%,#8c9099)"></div><h3>Mauris vel lacus vitae</h3><p>pede Fusce tellus Sed metus augue convallis et vehicula ut pulvinar eu ante Integer orci</p><span class="click">Click here</span></div>

  <footer class="abs footer">
    <div class="col" style="left:185px"><h4>Quick Links</h4><a href="#">About Us</a><a href="#">Job Seekers</a><a href="#">Employes</a><a href="#">Contact Us</a></div>
    <div class="col" style="left:317px"><h4>Resources</h4><a href="#">Support</a><a href="#">FAQ</a><a href="#">Blogs</a></div>
    <div class="col" style="left:442px"><h4>Newsletter Sign Up</h4><div>Please sign up here for latest offers</div><div class="email">Email address</div><div class="subscribe">SUBSCRIBE</div></div>
    <div class="col" style="left:659px"><h4>Contact Info</h4><div>48 Harbor Lane Suite 3 Austin 78701 TX</div><div class="phone">555.014.2290</div><div>info@brightlane.com</div></div>
  </footer>
  <div class="abs bottom-bar"><p>© 2015 Company Name &nbsp;All right reserved &nbsp;Term of Use</p></div>

</div>
</body>
</html>
```